8 x 8 Social Media Design - Tax, Accounting & Bookkeeping Service

Bright Path Ledger Group, Inc.

Tax, Accounting and Bookkeeping Services

“We provide our services, with you next mortgage in mind”

Special pricing available for all Mortgage Loan Customers!!

President / CEO Marcus Delaney

Primary service provider with over 27 years of experience

Call directly for more information: (240) 555-0193

Or email at: mdelaney@brightpathledger.com

```html
<!DOCTYPE html>
<html lang="en">
<head>
<meta charset="utf-8">
<title>Bright Path Ledger Group – Tax, Accounting &amp; Bookkeeping</title>
<link rel="stylesheet" href="https://fonts.googleapis.com/css2?family=Cinzel:wght@700;800&family=Playfair+Display:ital,wght@1,700&family=Poppins:ital,wght@0,400;0,600;0,700;1,400;1,700&display=swap">
<style>
  :root {
    --stage: #d9d9d9;
    --navy: #0f2a6b;
    --navy-deep: #0a1d4f;
    --royal: #1c3f99;
    --gold: #e0a82e;
    --gold-light: #f6d77c;
    --gold-dark: #b07a14;
    --cream: #fdf8ec;
    --white: #ffffff;
  }
  * { margin: 0; padding: 0; box-sizing: border-box; }
  html, body { width: 1200px; height: 2430px; overflow: hidden; background: var(--stage); }
  .canvas { position: relative; width: 1200px; height: 2430px; background: var(--stage); }
  .post {
    position: absolute; left: 0; top: 1230px; width: 1200px; height: 1200px; overflow: hidden;
    background: linear-gradient(120deg, var(--white) 0%, var(--cream) 35%, #f7e3a8 60%, #e9b94a 85%, #d89b22 100%);
    font-family: "Poppins", sans-serif;
  }
  .post-shapes, .badge-shapes { position: absolute; inset: 0; }
  .portrait {
    position: absolute; left: 740px; top: 40px; width: 460px; height: 743px;
    background: linear-gradient(180deg, rgba(26,27,34,0) 0%, #1a1b22 20%, #22242c 60%, #15161b 100%);
    border-radius: 180px 0 0 0;
  }
  .brand-name {
    position: absolute; left: 40px; top: 140px; width: 520px; text-align: center;
    font-family: "Cinzel", serif; font-weight: 700; font-size: 50px; line-height: 1.15; color: var(--navy);
  }
  .brand-mark {
    display: block; width: 34px; height: 34px; border-radius: 50%; background: var(--gold); margin: 0 auto 18px;
  }
  .headline {
    position: absolute; left: 57px; top: 350px; font-family: "Cinzel", serif; font-weight: 800;
    font-size: 52px; line-height: 54px; color: var(--gold); white-space: nowrap;
  }
  .subline {
    position: absolute; left: 57px; top: 462px; font-size: 23px; color: var(--white); line-height: 1; white-space: nowrap;
  }
  .photo {
    position: absolute; top: 514px; width: 307px; height: 245px; border: 7px solid var(--gold);
    border-radius: 16px; box-shadow: 0 0 0 2px var(--gold-light);
  }
  .photo-moving { left: 57px; background: linear-gradient(135deg, #e8ddd0, #b98b62 60%, #8a5c3a); }
  .photo-couple { left: 377px; background: linear-gradient(135deg, #c9d3dc, #6f8fb4 55%, #4a5a3a); }
  .badge-title {
    position: absolute; left: 175px; top: 768px; width: 300px; text-align: center;
    font-weight: 600; font-size: 40px; line-height: 40px; color: var(--navy);
  }
  .badge-note {
    position: absolute; left: 137px; top: 905px; width: 377px; text-align: center;
    font-weight: 700; font-size: 31px; line-height: 33px; color: var(--white); letter-spacing: 1px;
  }
  .person { position: absolute; left: 600px; top: 812px; width: 560px; text-align: center; }
  .person-name {
    font-family: "Playfair Display", serif; font-style: italic; font-weight: 700; font-size: 66px;
    line-height: 80px; color: var(--gold); white-space: nowrap;
  }
  .person-role { font-size: 44px; line-height: 56px; color: var(--white); letter-spacing: 1px; }
  .person-rule { height: 2px; width: 500px; margin: 8px auto 10px; background: var(--gold-light); opacity: .8; }
  .person-experience { font-style: italic; font-size: 42px; line-height: 50px; color: var(--white); }
  .person-experience strong { font-weight: 700; }
  .contact { position: absolute; left: 57px; line-height: 1; color: var(--gold); display: flex; align-items: center; gap: 20px; white-space: nowrap; }
  .contact-phone { top: 1036px; font-size: 44px; font-weight: 700; }
  .contact-email { top: 1094px; font-size: 36px; }
  .contact svg { width: 36px; height: 36px; flex: none; }
</style>
</head>
<body>
<div class="canvas">
  <section class="post">
    <div class="portrait" role="img" aria-label="Portrait of the president in a black hat and coat, seated"></div>

    <svg class="post-shapes" viewBox="0 0 1200 1200" aria-hidden="true">
      <defs>
        <linearGradient id="bandGrad" x1="0" x2="1">
          <stop offset="0" stop-color="#0f2a6b"/><stop offset="0.6" stop-color="#1c3f99"/><stop offset="1" stop-color="#0f2a6b"/>
        </linearGradient>
        <linearGradient id="footGrad" x1="0" y1="0" x2="1" y2="1">
          <stop offset="0" stop-color="#0a1d4f"/><stop offset="0.5" stop-color="#1c3f99"/><stop offset="1" stop-color="#0f2a6b"/>
        </linearGradient>
        <linearGradient id="goldGrad" x1="0" x2="1">
          <stop offset="0" stop-color="#b07a14"/><stop offset="0.5" stop-color="#f6d77c"/><stop offset="1" stop-color="#e0a82e"/>
        </linearGradient>
      </defs>
      <rect x="0" y="331" width="870" height="4" fill="url(#goldGrad)"/>
      <rect x="0" y="335" width="870" height="160" fill="url(#bandGrad)"/>
      <rect x="0" y="495" width="790" height="4" fill="url(#goldGrad)"/>
      <rect x="0" y="499" width="740" height="280" fill="#ffffff" opacity="0.85"/>
      <rect x="0" y="779" width="1200" height="4" fill="url(#goldGrad)"/>
      <rect x="0" y="783" width="1200" height="417" fill="url(#footGrad)"/>
      <path d="M0 1200 C 500 1196 900 1125 1200 1000 L1200 1030 C 900 1150 520 1198 80 1200 Z" fill="url(#goldGrad)"/>
      <path d="M80 1200 C 520 1198 900 1150 1200 1030 L1200 1200 Z" fill="#0a1d4f"/>
    </svg>

    <div class="brand-name"><span class="brand-mark"></span>Bright Path Ledger Group, Inc.</div>

    <h1 class="headline">TAX, ACCOUNTING AND<br>BOOKKEEPING SERVICES</h1>
    <p class="subline">We provide our services, with you next mortgage in mind</p>

    <div class="photo photo-moving" role="img" aria-label="Photo of a happy couple unpacking moving boxes in a new home"></div>
    <div class="photo photo-couple" role="img" aria-label="Photo of two smiling women in front of a house"></div>

    <svg class="badge-shapes" viewBox="0 0 1200 1200" aria-hidden="true">
      <defs>
        <radialGradient id="sealGrad" cx="0.4" cy="0.35" r="0.7">
          <stop offset="0" stop-color="#fbe7a6"/><stop offset="0.6" stop-color="#e0a82e"/><stop offset="1" stop-color="#b07a14"/>
        </radialGradient>
      </defs>
      <circle cx="325" cy="868" r="146" fill="url(#sealGrad)"/>
      <circle cx="325" cy="868" r="134" fill="none" stroke="#fbe7a6" stroke-width="2"/>
      <path d="M57 880 L140 880 L140 984 L57 984 L95 932 Z" fill="#1c3f99" stroke="#e0a82e" stroke-width="4"/>
      <path d="M590 880 L510 880 L510 984 L590 984 L552 932 Z" fill="#1c3f99" stroke="#e0a82e" stroke-width="4"/>
      <rect x="137" y="898" width="377" height="84" fill="#0f2a6b" stroke="#e0a82e" stroke-width="5"/>
    </svg>

    <p class="badge-title">SPECIAL<br>PRICING<br>AVAILABLE</p>
    <p class="badge-note">FOR MORTGAGE<br>LOAN CUSTOMERS!!</p>

    <div class="person">
      <p class="person-name">Marcus Delaney</p>
      <p class="person-role">PRESIDENT / CEO</p>
      <div class="person-rule"></div>
      <p class="person-experience"><strong>27 years</strong> of experience</p>
    </div>

    <p class="contact contact-phone">
      <svg viewBox="0 0 24 24" aria-hidden="true"><path fill="#ffffff" d="M6.6 10.8a15.1 15.1 0 0 0 6.6 6.6l2.2-2.2c.3-.3.7-.4 1-.2 1.1.4 2.3.6 3.6.6.6 0 1 .4 1 1V20c0 .6-.4 1-1 1C10.6 21 3 13.4 3 4c0-.6.4-1 1-1h3.5c.6 0 1 .4 1 1 0 1.3.2 2.5.6 3.6.1.3 0 .7-.2 1z"/></svg>
      (240) 555-0193
    </p>
    <p class="contact contact-email">
      <svg viewBox="0 0 24 24" aria-hidden="true"><rect x="2" y="5" width="20" height="14" fill="none" stroke="#ffffff" stroke-width="2"/><path d="M2 5l10 8 10-8" fill="none" stroke="#ffffff" stroke-width="2"/></svg>
      mdelaney@brightpathledger.com
    </p>
  </section>
</div>
</body>
</html>
```